Short fill E liquid label UK. 100ml Nicotine free

Short Fill e liquid label (UK). The BRAND name is "Lumora" (Logo uploaded).Looking to release a new range under the Lumora name. The new range will be called "Glitch". A range of Liquids mixed together. Needs to look cool, stand out and funky but not too crazy. The range will have 10 different flavours so will need these all done, a simple flavour name towards bottom of label will do for this or a different colour for each.Any warnings ( requirements by law) etc and company address/details etc need to have a place on the labels. Basically need to be E liquid compliant label but all are nicotine free so not so many law requirements.Label Size will be 120mm( wide)x 60mm(high), bottle diameter is 41mm .

The 10 flavour names are as follows so will need appropriate colours for each flavour:
Frostbite ( a menthol and custard mix )
Fruit loop ( a mixed fruit mix )
Smooth custard ( custard based mix )
Strawberry Shake ( Strawberry milkshake mix )
Cookie Jar ( a cookie based mix )
Black ice ( a liquorice and menthol mix )
Madagascan breeze ( Mainly vanilla based mix )
Choc shake ( chocolate milkshake )
nutter ( a peanut butter and banana mix )
Cool currant ( blackcurrant and menthol mix )

Requirements
Must have
• The info and warnings that need to be on the bottle are as follows:
• signs that need to be on bottle:
• 18+ sign
• Caution sign (!)
• United kingdom flag with" made in the united kingdom written underneath"
• text that needs to be on the bottle:
• Nicotine free eliquid. (in bold lettering )
• Keep out of the reach of children. Always
• read the label before use.
• If swallowed consult a doctor if feeling unwell . In case of contact with eyes consult a doctor.
• Dispose of in a responsible manner.
• Store in a dark place at room temperature.
• Ingredients:
• Vegetable glycerin, Propylene glycol, Flavourings.
• PG/VG ratio 70/30 %

```html
<!DOCTYPE html>
<html lang="en">
<head>
<meta charset="utf-8">
<title>Lumora Glitch – Frostbite label</title>
<link rel="stylesheet" href="https://fonts.googleapis.com/css2?family=Open+Sans:wght@400;600;700;800&display=swap">
<style>
  :root {
    --page: #ffffff;
    --label-dark: #050505;
    --label-mid: #1c1c1c;
    --ink: #ffffff;
    --flavour: #8fd98b;
    --flavour-deep: #0b0b0b;
    --box: #ffffff;
    --box-ink: #111111;
    --flag-blue: #012169;
    --flag-red: #c8102e;
  }
  * { box-sizing: border-box; margin: 0; padding: 0; }
  html, body { width: 849px; height: 1200px; overflow: hidden; background: var(--page); }
  body { position: relative; font-family: "Open Sans", Arial, sans-serif; color: var(--ink); }

  .label {
    position: absolute; left: 24px; top: 400px; width: 800px; height: 400px;
    background:
      repeating-linear-gradient(-28deg, rgba(255,255,255,0.035) 0 1px, transparent 1px 7px),
      radial-gradient(ellipse at 55% 45%, var(--label-mid) 0%, var(--label-dark) 70%);
    box-shadow: 0 6px 18px rgba(0,0,0,0.35);
    overflow: hidden;
  }
  .column { position: absolute; text-align: center; }
  .column--safety { left: 24px; width: 220px; top: 38px; }
  .column--info { left: 557px; width: 220px; top: 40px; }

  .heading { font-weight: 600; font-size: 16px; margin-bottom: 14px; }
  .safety-text { font-size: 13px; line-height: 17px; margin-bottom: 16px; }
  .info-text { font-size: 13px; line-height: 16px; }
  .nicotine { font-weight: 700; font-size: 15.5px; margin-top: 22px; }
  .keep-out { font-size: 11px; line-height: 16px; margin-top: 14px; }

  .batch-box {
    position: absolute; left: 33px; top: 258px; width: 203px; height: 37px;
    background: var(--box); color: var(--box-ink);
    font-size: 10px; font-weight: 600; font-style: italic; line-height: 14px; padding: 4px 7px;
  }
  .origin { position: absolute; left: 33px; top: 312px; width: 210px; height: 52px; }
  .origin svg { position: absolute; left: 0; top: 0; }
  .origin-text { position: absolute; left: 106px; top: 10px; width: 104px; text-align: center; font-size: 13px; line-height: 17px; }

  .brand-tab {
    position: absolute; left: 333px; top: -4px; width: 134px; height: 126px;
    display: flex; align-items: center; justify-content: center;
  }
  .brand-tab svg { position: absolute; inset: 0; }
  .brand-name { position: relative; color: var(--box-ink); font-weight: 700; font-size: 26px; margin-top: -8px; }

  .range-title {
    position: absolute; left: 247px; top: 178px; width: 306px; text-align: center;
    font-weight: 800; font-size: 74px; line-height: 82px; text-transform: uppercase; letter-spacing: 1px;
  }
  .range-sub {
    position: absolute; left: 247px; top: 266px; width: 306px; text-align: center;
    font-weight: 700; font-size: 11.5px; letter-spacing: 3px;
  }
  .flavour {
    position: absolute; left: 296px; top: 308px; width: 206px; height: 51px;
    border: 2px solid var(--flavour); background: var(--flavour-deep);
  }
  .flavour-icon { position: absolute; left: 0; top: 0; width: 80px; height: 47px; background: var(--flavour);
    clip-path: polygon(0 0, 100% 0, 80% 100%, 0 100%); }
  .flavour-name {
    position: absolute; left: 72px; top: 0; width: 130px; height: 47px; line-height: 47px; text-align: center;
    color: var(--flavour); font-weight: 800; font-size: 20px; text-transform: uppercase;
  }

  .age-badges { position: absolute; left: 608px; top: 223px; width: 126px; height: 56px; }
  .barcode-box {
    position: absolute; left: 575px; top: 295px; width: 184px; height: 67px;
    background: var(--box); color: var(--box-ink); font-size: 25px;
    display: flex; align-items: center; justify-content: center;
  }
</style>
</head>
<body>
  <section class="label">
    <div class="column column--safety">
      <p class="heading">Read the label before use.</p>
      <p class="safety-text">If swallowed consult a doctor if feeling unwell . In case of contact with eyes consult a doctor.</p>
      <p class="safety-text">Dispose of in a responsible manner.</p>
      <p class="safety-text">Store in a dark place at room temperature.</p>
    </div>
    <div class="batch-box">Best Before:<br>Batch Number:</div>
    <div class="origin">
      <svg width="86" height="52" viewBox="0 0 60 36" aria-label="United Kingdom flag">
        <rect width="60" height="36" fill="var(--flag-blue)"/>
        <path d="M0 0L60 36M60 0L0 36" stroke="#fff" stroke-width="7"/>
        <path d="M0 0L60 36M60 0L0 36" stroke="var(--flag-red)" stroke-width="2.5"/>
        <path d="M30 0V36M0 18H60" stroke="#fff" stroke-width="11"/>
        <path d="M30 0V36M0 18H60" stroke="var(--flag-red)" stroke-width="6"/>
      </svg>
      <p class="origin-text">Made in the United Kingdom</p>
    </div>

    <div class="brand-tab">
      <svg width="134" height="126" viewBox="0 0 134 126">
        <path d="M4 0H130V94L67 123L4 94Z" fill="var(--box)"/>
        <path d="M11 0V90L67 116L123 90V0" fill="none" stroke="var(--box-ink)" stroke-width="3"/>
      </svg>
      <span class="brand-name">Lumora</span>
    </div>
    <h1 class="range-title">Glitch</h1>
    <p class="range-sub">E-CIGARETTES &amp; LIQUID</p>
    <div class="flavour">
      <div class="flavour-icon" role="img" aria-label="Mint leaf flavour icon"></div>
      <span class="flavour-name">Frostbite</span>
    </div>

    <div class="column column--info">
      <p class="heading">ingredients:</p>
      <p class="info-text">Vegetable glycerin, Propylene glycol, Flavourings.<br>PG/VG ratio 70/30 %</p>
      <p class="nicotine">Nicotine free eliquid.</p>
      <p class="keep-out">Keep out of the reach of children.<br>Always</p>
    </div>
    <svg class="age-badges" viewBox="0 0 126 56" aria-label="18+ and caution signs">
      <circle cx="27" cy="28" r="25" fill="#fff" stroke="#000" stroke-width="1.5"/>
      <text x="27" y="37" text-anchor="middle" font-family="Open Sans, sans-serif" font-weight="700" font-size="24" fill="#000">18+</text>
      <path d="M93 5L120 52H66Z" fill="none" stroke="#fff" stroke-width="3.5" stroke-linejoin="round"/>
      <rect x="90.8" y="20" width="4.4" height="19" rx="1" fill="#fff"/>
      <circle cx="93" cy="45" r="2.6" fill="#fff"/>
    </svg>
    <div class="barcode-box">bar code</div>
  </section>
</body>
</html>
```